Moravel Aesthetic Doctor

I require an elegant, luxurious looking business card for my aesthetic business. I am a doctor and that will set me aside from competitors. I am planning to provide home and spa based treatments to clients with high expectations. I have attached my logo.

```html
<!DOCTYPE html>
<html lang="en">
<head>
<meta charset="utf-8">
<title>Moravel Aesthetic Doctor – Business Card</title>
<link href="https://fonts.googleapis.com/css2?family=Work+Sans:wght@400;500;600&display=swap" rel="stylesheet">
<style>
  :root {
    --backdrop: #d2d2ce;
    --paper: #f0f0ef;
    --charcoal: #2b2b2b;
    --charcoal-soft: #3a3a3a;
    --accent: #1ea0e6;
    --accent-line: #7cc8f0;
    --edge: #3b8fd6;
    --ink: #3d3d3d;
    --silver: #8a8a8a;
    --light-text: #f2f2f2;
  }
  * { margin: 0; padding: 0; box-sizing: border-box; }
  html, body { width: 1200px; height: 1058px; overflow: hidden; }
  body {
    background: var(--backdrop);
    font-family: "Work Sans", Arial, sans-serif;
    position: relative;
  }
  .card {
    position: absolute;
    width: 600px;
    height: 343px;
    box-shadow: 0 16px 30px rgba(0,0,0,.18);
  }
  /* Front */
  .card--front {
    left: 90px; top: 150px;
    background: var(--paper);
    border-bottom: 5px solid var(--edge);
    display: flex;
    align-items: center;
    padding: 0 50px;
  }
  .brand {
    display: flex; align-items: center; gap: 14px;
    width: 250px;
  }
  .brand__dot {
    width: 44px; height: 44px; flex: none;
    border-radius: 50%;
    background: var(--accent);
  }
  .brand__name {
    font-weight: 500; font-size: 19px; line-height: 1.25;
    letter-spacing: .08em; text-transform: uppercase;
    color: var(--silver);
  }
  .divider {
    width: 1px; height: 120px;
    background: var(--accent-line);
    margin: 0 26px 0 10px;
  }
  .contact { color: var(--ink); font-size: 13px; line-height: 1.45; }
  .contact__name { color: var(--accent); font-weight: 600; font-size: 15px; margin-bottom: 2px; }
  .contact__row { display: flex; align-items: center; gap: 7px; }
  .contact__row svg { width: 10px; height: 10px; fill: var(--accent); flex: none; }
  /* Back */
  .card--back {
    left: 510px; top: 560px;
    background: var(--charcoal);
    border-bottom: 5px solid var(--edge);
    overflow: hidden;
  }
  .card__decoration {
    position: absolute; inset: 0;
    background: radial-gradient(ellipse at 70% 30%, var(--charcoal-soft) 0%, var(--charcoal) 65%);
  }
  .back-brand {
    position: absolute; left: 0; right: 0; top: 95px;
    display: flex; align-items: center; justify-content: center; gap: 18px;
  }
  .back-brand__ring {
    width: 60px; height: 60px; border-radius: 50%;
    border: 3px solid #1e1e1e;
  }
  .back-brand__name {
    font-weight: 500; font-size: 30px; letter-spacing: .08em;
    text-transform: uppercase; color: var(--silver);
  }
  .services {
    position: absolute; left: 0; right: 0; top: 210px;
    text-align: center; color: var(--light-text);
    font-size: 15px; line-height: 1.5; letter-spacing: .04em;
  }
  .services .sep { color: var(--accent); margin: 0 5px; }
  .services__tag { text-transform: uppercase; letter-spacing: .08em; font-size: 14px; }
</style>
</head>
<body>
  <section class="card card--front" aria-label="Business card front">
    <div class="brand">
      <span class="brand__dot"></span>
      <span class="brand__name">Moravel Aesthetic Doctor</span>
    </div>
    <span class="divider"></span>
    <div class="contact">
      <p class="contact__name">Dr Elin Varga MRCPCH MD</p>
      <p>Australasian Diploma</p>
      <p>of Aesthetic Medicine</p>
      <p class="contact__row"><svg viewBox="0 0 10 10"><path d="M2 0l2 2-1 1.5c.6 1.4 1.6 2.4 3 3L7.5 5.5l2 2L8 10C4 9.5.5 6 0 2z"/></svg>0800 457 319</p>
      <p class="contact__row"><svg viewBox="0 0 10 10"><path d="M0 2h10v6H0z M0 2l5 3.5L10 2" /></svg>elin@moravel.co.nz</p>
      <p class="contact__row"><svg viewBox="0 0 10 10"><circle cx="5" cy="5" r="5"/></svg>www.moravel.co.nz</p>
    </div>
  </section>

  <section class="card card--back" aria-label="Business card back">
    <div class="card__decoration" role="img" aria-label="Faint flowing-hair silhouette decoration in dark grey"></div>
    <div class="back-brand">
      <span class="back-brand__ring"></span>
      <span class="back-brand__name">Moravel Aesthetic Doctor</span>
    </div>
    <div class="services">
      <p>Dermal injectables<span class="sep">|</span>Plasma facials<span class="sep">|</span>Microneedling</p>
      <p>Skin boosters<span class="sep">|</span>Excessive sweating</p>
      <p class="services__tag">Home and spa based treatments</p>
    </div>
  </section>
</body>
</html>
```